Bluefern Business Services needs a new interactive and interesting website

We need an interesting, professional, modern and functional company website for Bluefern Business Services - a young IT Services company based out of Chennai, India.

Bluefern Business Services is a fully owned subsidiary of Marlow Goods, one of the world's leading direct to consumer wine merchant.

We already have a registered company logo which must feature in the website.

We conceive, design, develop, test, implement and support IT solutions across the entire Marlow Goods IT landscape. For ex : We currently run about 25 e-commerce websites for Marlow Goods on ATG and Dot Net.

We would like to see our corporate colors used in the website. (Burgundy wine and wine green - source: www.bluefernbs-site.com)

We are looking at this website to communicate a fun, friendly and professionally managed company - reaching out to career seekers, prospective customers and general public.

For reference - The company name 'Bluefern' is an inspiration from the Marlow Goods lineage.

The second image with the world map is stickered on our main entrance to the office, I am not sure where this can be used -just putting it out there..

Please note that there are only a few more days to submit designs for this contest  !

I would appreciate if you can help posting your designs in time for our review and consideration.

Thanks.

Reason: Thanks for your inputs. We have a number of designers and a lot to digest and work with in the past few days. There has been a rush of new designs in the last few days Hence we will require more time to process these and make our decision. Hence i am requesting the contest to be open for more days. Regards, Tarun

Target Market(s)

Prospective job seekers who want to know more about the company and also wish to apply for a job vacancy
People wanting to know more about the company in general and our progress
People who want to see what we offer and how we can help them too - prospective customers
Companies that are interested in our IT Captive journey and are looking for a business opportunity

Industry/Entity Type

E-Commerce

Requirements
Must have
• Log In/ Register facility acting as a Single Sign on for Intranet (Employees)

Facility to post job vacancies (with an expiry date) and enable people to apply for a role and upload their CV/Resume.

Facility to Review Job applications

Facility for website visitors to contact Bluefern business Services via an online 'Contact Us' form with a split of job seekers and business opportunities

Gallery facility to upload pictures regarding company events
Nice to have
• Less Cluttered and contemporary design
Some Wine/Vineyard inspirations will be good but not too much, the company is an IT services company

```html
<!DOCTYPE html>
<html lang="en">
<head>
<meta charset="utf-8">
<title>Bluefern Business Services</title>
<link rel="stylesheet" href="https://fonts.googleapis.com/css2?family=Source+Sans+3:wght@400;600;700&family=Arimo:wght@400&display=swap">
<style>
  :root {
    --burgundy: #8c0f4a;
    --burgundy-dark: #6e0a39;
    --cream-top: #f6f2ea;
    --cream-bottom: #e6dfd1;
    --paper: #f1f0ee;
    --text-grey: #6f6a66;
    --nav-grey: #e4e1da;
    --nav-text: #3c3a38;
    --green-top: #84853c;
    --green-bottom: #a9b84e;
    --footer: #3b3b3b;
    --white: #ffffff;
  }
  * { box-sizing: border-box; margin: 0; padding: 0; }
  html, body { width: 1200px; height: 923px; overflow: hidden; }
  body {
    position: relative;
    font-family: "Source Sans 3", sans-serif;
    background: var(--paper);
  }
  .hero-band {
    position: absolute; left: 0; top: 0; width: 1200px; height: 623px;
    background: linear-gradient(180deg, var(--cream-top) 0%, #f1ece2 45%, var(--cream-bottom) 100%);
    border-bottom: 4px solid var(--white);
  }
  .content-band {
    position: absolute; left: 0; top: 627px; width: 1200px; height: 220px;
    background: repeating-linear-gradient(135deg, #f3f3f2 0 3px, #ecebea 3px 5px);
  }
  .brand {
    position: absolute; left: 120px; top: 40px;
    display: flex; align-items: center; gap: 14px;
  }
  .brand-mark { width: 58px; height: 58px; border-radius: 50%; background: var(--burgundy); }
  .brand-name {
    font-weight: 700; font-size: 76px; line-height: 1; color: var(--burgundy);
    letter-spacing: -1px;
  }
  .utility-links {
    position: absolute; right: 119px; top: 37px;
    display: flex; font-size: 16px; color: var(--burgundy-dark);
  }
  .utility-links span { padding: 0 12px; }
  .utility-links span + span { border-left: 1px dotted #c9bfb3; padding-right: 0; }
  .search {
    position: absolute; left: 840px; top: 81px; width: 241px; height: 33px;
    background: var(--white); border: 1px solid #d6d2cc;
    font-size: 14px; color: #666; padding: 8px 12px;
  }
  .search svg { position: absolute; right: 9px; top: 8px; }
  .main-nav { position: absolute; top: 163px; left: 0; width: 1200px; height: 54px; }
  .nav-item {
    position: absolute; top: 0; height: 54px;
    background: var(--nav-grey); border-bottom: 4px solid var(--burgundy);
    font-family: "Arimo", sans-serif; font-size: 16px; color: var(--nav-text);
    display: flex; align-items: center; justify-content: center; letter-spacing: 0.3px;
  }
  .nav-item.active { background: var(--white); }
  .bottle-visual {
    position: absolute; left: 118px; top: 290px; width: 90px; height: 310px;
    border-radius: 14px 14px 6px 6px;
    background: linear-gradient(90deg, #1e1a1c, #3b3437 50%, #1a1618);
  }
  .hero-title {
    position: absolute; left: 292px; top: 322px;
    font-size: 29px; font-weight: 600; color: var(--burgundy);
  }
  .hero-text {
    position: absolute; left: 292px; top: 376px; width: 290px;
    font-size: 14.5px; line-height: 26px; color: var(--text-grey);
  }
  .read-more {
    position: absolute; left: 292px; top: 473px; width: 126px; height: 42px;
    background: var(--burgundy); border: 2px solid #b23a72; border-radius: 3px;
    color: var(--white); font-size: 17px; display: flex; align-items: center; justify-content: center;
  }
  .event-photo {
    position: absolute; left: 659px; top: 287px; width: 422px; height: 336px;
    background: linear-gradient(135deg, #e9e6e1 0%, #cfcac3 55%, #7d7c80 100%);
  }
  .slider-arrow { position: absolute; top: 435px; }
  .events-panel {
    position: absolute; left: 659px; top: 623px; width: 422px; height: 198px;
    background: linear-gradient(180deg, var(--green-top), var(--green-bottom));
    color: var(--white); padding: 16px 20px 0 19px;
  }
  .events-panel::before {
    content: ""; position: absolute; left: 52px; top: -10px;
    border-left: 10px solid transparent; border-right: 10px solid transparent;
    border-bottom: 10px solid var(--green-top);
  }
  .events-title {
    font-size: 22px; font-weight: 400; padding-bottom: 10px;
    border-bottom: 1px solid rgba(255,255,255,0.3); margin-bottom: 14px;
  }
  .events-text { font-size: 14.3px; line-height: 24px; font-weight: 600; }
  .welcome-title {
    position: absolute; left: 120px; top: 659px;
    font-size: 23px; font-weight: 400; color: #3d3a38;
  }
  .welcome-title em { font-style: normal; color: var(--burgundy); }
  .welcome-text {
    position: absolute; left: 120px; top: 702px; width: 470px;
    font-size: 14px; line-height: 24px; color: var(--text-grey);
  }
  .site-footer {
    position: absolute; left: 0; top: 847px; width: 1200px; height: 76px;
    background: var(--footer);
  }
  .copyright {
    position: absolute; left: 119px; top: 31px;
    font-family: "Arimo", sans-serif; font-size: 13px; color: var(--white);
  }
  .social { position: absolute; top: 24px; width: 34px; height: 34px; }
  .social.one { left: 894px; background: #4a5a9c; }
  .social.two { left: 940px; background: #3b9ad3; }
  .social.three { left: 985px; background: #f06a1e; }
  .social.four { left: 1030px; background: #d4242a; }
</style>
</head>
<body>
  <div class="hero-band"></div>
  <div class="content-band"></div>

  <header>
    <div class="brand"><span class="brand-mark"></span><span class="brand-name">bluefern</span></div>
    <div class="utility-links"><span>Careers</span><span>Contact</span></div>
    <div class="search">Search..
      <svg width="14" height="14" viewBox="0 0 14 14"><circle cx="5.5" cy="5.5" r="4.3" fill="none" stroke="#999" stroke-width="1.8"/><line x1="8.6" y1="8.6" x2="13" y2="13" stroke="#999" stroke-width="2"/></svg>
    </div>
    <nav class="main-nav">
      <div class="nav-item active" style="left:121px;width:111px">HOME</div>
      <div class="nav-item" style="left:273px;width:127px">ABOUT US</div>
      <div class="nav-item" style="left:446px;width:126px">CLIENTS</div>
      <div class="nav-item" style="left:607px;width:127px">SERVICES</div>
      <div class="nav-item" style="left:772px;width:127px">CAREERS</div>
      <div class="nav-item" style="left:939px;width:142px">CONTACT US</div>
    </nav>
  </header>

  <section class="hero">
    <div class="bottle-visual" role="img" aria-label="Bottle of red wine with an ornate white label"></div>
    <h1 class="hero-title">Aenean nec urna elitin</h1>
    <p class="hero-text">Duis autem vel eum iriure dolor in hendrerit in vulputate velit esse molestie consequat, vel ill um dolore eu feugiat nulla facilisisat vero.</p>
    <div class="read-more">READ MORE</div>
    <div class="event-photo" role="img" aria-label="Team meeting in a bright office with a presenter and a monitor showing company status charts"></div>
    <svg class="slider-arrow" style="left:672px" width="30" height="30" viewBox="0 0 30 30"><circle cx="15" cy="15" r="13" fill="rgba(0,0,0,0.15)" stroke="#fff" stroke-width="2"/><path d="M17 9 L11 15 L17 21 M11 15 H21" fill="none" stroke="#fff" stroke-width="2.4"/></svg>
    <svg class="slider-arrow" style="left:1036px" width="30" height="30" viewBox="0 0 30 30"><circle cx="15" cy="15" r="13" fill="rgba(0,0,0,0.15)" stroke="#fff" stroke-width="2"/><path d="M13 9 L19 15 L13 21 M19 15 H9" fill="none" stroke="#fff" stroke-width="2.4"/></svg>
  </section>

  <section class="welcome">
    <h2 class="welcome-title">Welcome to <em>Bluefern</em></h2>
    <p class="welcome-text">Typi non habent claritatem insitam; est usus legentis nis qui facit eorum clarita tem. Investigationes demonstraveruilectores legere me lius quod ii legunt saei pius. Claritas est etiaprocessus dynamicus, qui sequitur mutationem . Nullam v arius eleifend elit, nec sollicitudin est vulputate a. Suspendisse non elit ante.</p>
  </section>

  <aside class="events-panel">
    <h3 class="events-title">Company Events</h3>
    <p class="events-text">Typi non habent claritatem insitam; est usus legentis nis qui facit eorum claritatem. Investigationes demonstraveruilecto res legere me lius quod ii legunt saepius. Claritas est etiapro cessus dynamicus, qui sequitur mutationem .</p>
  </aside>

  <footer class="site-footer">
    <p class="copyright">Copyright ©2013. All Rights Reserved.</p>
    <span class="social one"></span>
    <span class="social two"></span>
    <span class="social three"></span>
    <span class="social four"></span>
  </footer>
</body>
</html>
```